BRELWINCare.co.uk - Mental Health Clinic for Child and Adolescents

Updated 29/01/2018***
I am not sure you guys are getting the idea regards to the opening page / homescreen layout. Can you look at the new images I have uploaded (page 5, 6 and 7) These are some of the layouts I like but to incorporate my chosen images, with the BRELWIN commissioner, buttons and a sliding header bar.
I have written a strong brief, I am looking for a website, preferably wordpress as i know they are easy to maintain. I am looking for a one page site, with the top / opening page being full screen image with drop down categories. I have made a rough design, see full brief in word doc attached, there is some freedom to play around with the design aspect but it will need to relay all the content provided. I like a minimal feel. I have also attached some images that may be useful, but will need a new logo for BRELWIN Care. I have attached some logo idea's, it is up to you decide whether you want to use them.
I would prefer the homepage as full screen image, and the categories offered as a drop down or over the main image.
I have also attached linked to some competitors websites:
https://www.vorimant-health.co.uk/
http://www.qlbn.org.uk/
Industry/Entity Type
Clinic
Number of Pages Required
1 page
Font styles to use
Look and feel
Each slider illustrates characteristics of the customer's brand and the style your logo design should communicate.

```html
<!DOCTYPE html>
<html lang="en">
<head>
<meta charset="utf-8">
<title>BRELWIN Care – Where Young Minds Matter</title>
<link href="https://fonts.googleapis.com/css2?family=Open+Sans:wght@400;600&family=Poppins:wght@400;500&family=Yellowtail&display=swap" rel="stylesheet">
<style>
  :root {
    --green: #0f9a80;
    --purple: #6b1f6f;
    --ink: #1f1a24;
    --white: #ffffff;
    --rule: #e3e3e3;
    --icon: #333333;
    --link: #33d0b0;
    --hero-top: #cfe3e0;
    --hero-mid: #b7aaa4;
    --hero-bottom: #3a1638;
  }
  * { box-sizing: border-box; margin: 0; padding: 0; }
  html, body { width: 1200px; height: 600px; overflow: hidden; }
  body { position: relative; font-family: "Open Sans", Arial, sans-serif; background: var(--white); }

  .hero-photo {
    position: absolute; left: 66px; top: 0; width: 1134px; height: 600px;
    background:
      linear-gradient(180deg, rgba(58,22,56,0) 55%, rgba(58,22,56,0.85) 100%),
      linear-gradient(100deg, #8a6e60 0%, var(--hero-top) 35%, #e4eeec 55%, var(--hero-mid) 80%, #d9d2c6 100%);
  }

  .brand {
    position: absolute; left: 0; top: 0; width: 155px; height: 86px;
    background: var(--white); display: flex; flex-direction: column; justify-content: center; padding-left: 6px;
  }
  .brand-name { font-weight: 600; font-size: 24px; line-height: 28px; color: var(--purple); letter-spacing: 0.5px; display: flex; align-items: center; gap: 6px; margin-left: 14px; white-space: nowrap; }
  .brand-dot { width: 12px; height: 12px; border-radius: 50%; background: var(--green); }
  .brand-tagline { font-weight: 600; font-size: 10px; line-height: 14px; color: var(--purple); margin-top: 6px; white-space: nowrap; }

  .menu-toggle {
    position: absolute; left: 0; top: 86px; width: 155px; height: 87px;
    background: var(--green); display: flex; align-items: center; color: var(--white);
    font-size: 14px;
  }
  .menu-toggle svg { margin: 0 40px 0 18px; }

  .side-nav { position: absolute; left: 0; top: 173px; width: 66px; height: 427px; background: var(--white); list-style: none; }
  .side-nav li { height: 82px; border-bottom: 1px solid var(--rule); display: flex; align-items: center; justify-content: center; }

  .hero-title {
    position: absolute; left: 308px; top: 222px; width: 600px; height: 72px;
    text-align: center; white-space: nowrap;
    font-family: "Yellowtail", "Brush Script MT", cursive; font-weight: 400;
    font-size: 60px; line-height: 72px; color: var(--ink);
  }
  .hero-lead {
    position: absolute; left: 378px; top: 298px; width: 460px;
    text-align: center; white-space: nowrap;
    font-size: 12px; line-height: 20px; color: var(--ink);
  }

  .audience-links { position: absolute; top: 366px; left: 453px; display: flex; gap: 24px; }
  .audience-link {
    width: 136px; height: 32px; border-radius: 16px; display: flex; align-items: center;
    color: var(--white); font-size: 12.5px; text-decoration: none; position: relative; overflow: hidden;
  }
  .audience-link--parents { background: linear-gradient(112deg, var(--green) 0 76%, var(--white) 76% 100%); }
  .audience-link--commissioners { background: linear-gradient(112deg, var(--purple) 0 76%, var(--white) 76% 100%); }
  .audience-link span { width: 104px; text-align: center; white-space: nowrap; }
  .audience-link svg { position: absolute; right: 11px; top: 10px; }

  .site-footer {
    position: absolute; left: 66px; width: 1134px; top: 569px; text-align: center; white-space: nowrap;
    font-family: "Poppins", Arial, sans-serif; font-size: 11px; line-height: 16px; color: var(--white);
  }
  .site-footer a { color: var(--link); text-decoration: none; }
</style>
</head>
<body>
  <div class="hero-photo" role="img" aria-label="Photo of a young girl talking with a smiling counsellor in a bright room"></div>

  <header class="brand">
    <div class="brand-name"><span class="brand-dot"></span>BRELWIN</div>
    <div class="brand-tagline">Where Young Minds Matter</div>
  </header>

  <div class="menu-toggle">
    <svg width="28" height="20" viewBox="0 0 28 20" fill="none" stroke="#fff" stroke-width="2.2">
      <line x1="0" y1="2" x2="28" y2="2"/><line x1="0" y1="10" x2="28" y2="10"/><line x1="0" y1="18" x2="28" y2="18"/>
    </svg>
    MENU
  </div>

  <ul class="side-nav">
    <li aria-label="Notes"><svg width="30" height="30" viewBox="0 0 30 30" fill="none" stroke="var(--icon)" stroke-width="1.3"><rect x="4" y="5" width="19" height="22"/><path d="M7 3v4M11 3v4M15 3v4M19 3v4M8 13h9M8 17h6M8 21h8"/><path d="M26 9l-9 12-2 1 1-2 9-12z"/></svg></li>
    <li aria-label="Team"><svg width="34" height="30" viewBox="0 0 34 30" fill="none" stroke="var(--icon)" stroke-width="1.3"><circle cx="17" cy="10" r="5"/><circle cx="7" cy="13" r="3.5"/><circle cx="27" cy="13" r="3.5"/><path d="M8 28c0-6 4-10 9-10s9 4 9 10M1 28c0-5 3-8 6-8M33 28c0-5-3-8-6-8"/></svg></li>
    <li aria-label="Resources"><svg width="30" height="30" viewBox="0 0 30 30" fill="none" stroke="var(--icon)" stroke-width="1.3"><path d="M4 8l4-4 18 18-4 4z"/><path d="M9 9l2-2M13 13l2-2M17 17l2-2"/><path d="M22 4l4 4-16 16-5 1 1-5z"/></svg></li>
    <li aria-label="Contact"><svg width="28" height="28" viewBox="0 0 28 28" fill="none" stroke="var(--icon)" stroke-width="1.3"><path d="M6 3l5 5-3 3c1 3 5 7 8 8l3-3 5 5-3 3C13 24 4 15 3 6z"/></svg></li>
    <li aria-label="Services"><svg width="32" height="30" viewBox="0 0 32 30" fill="none" stroke="var(--icon)" stroke-width="1.3"><rect x="3" y="3" width="26" height="24"/><path d="M3 8h26M6 12h20M6 16h8M6 20h8M6 24h8M17 16h9v8h-9z"/></svg></li>
  </ul>

  <h1 class="hero-title">Education Templte</h1>
  <p class="hero-lead">BRELWIN Care was formed with a vision to provide the very<br>best BRELWIN assessments, therapy and aftercare.</p>

  <nav class="audience-links">
    <a class="audience-link audience-link--parents" href="#parents"><span>Parewts</span>
      <svg width="16" height="12" viewBox="0 0 16 12" fill="none" stroke="var(--green)" stroke-width="1.5"><path d="M0 6h15M10 1l5 5-5 5"/></svg></a>
    <a class="audience-link audience-link--commissioners" href="#commissioners"><span>Commissioners</span>
      <svg width="16" height="12" viewBox="0 0 16 12" fill="none" stroke="var(--purple)" stroke-width="1.5"><path d="M0 6h15M10 1l5 5-5 5"/></svg></a>
  </nav>

  <footer class="site-footer">© 2018 All Rights Reserved.<a href="#">brelwincare.com</a></footer>
</body>
</html>
```